Business Card Design

We provide services doing multiple jobs in the construction industry.Please note: The company name needs to be ROCK SOLID BUILDING SERVICESAttached logo was an example of what we wanted. Can you change up the colors?

Industry/Entity Type

Construction

Contact Information for Business Card

ROCK SOLID BUILDING SERVICES5401 HUDSON BEND RDAUSTIN, TX 78734(512)243-6854ROCKSOLIDBUILDINGSERVICES@GMAIL.COM

```html
<!DOCTYPE html>
<html lang="en">
<head>
<meta charset="utf-8">
<title>Pearlwood Framing Works — Business Card</title>
<link rel="stylesheet" href="https://fonts.googleapis.com/css2?family=Cinzel:wght@400;700&family=Arimo:wght@400&display=swap">
<style>
  :root {
    --page-bg: #e9e6e2;
    --card-white: #ffffff;
    --card-black: #000000;
    --frame-navy: #2a2a6e;
    --ink-light: #f2f2f2;
    --ink-dark: #1d2a5c;
  }
  * { margin: 0; padding: 0; box-sizing: border-box; }
  html, body {
    width: 1200px; height: 960px; overflow: hidden;
    background: var(--page-bg);
  }
  .canvas {
    width: 1200px; height: 960px;
    display: flex; align-items: center; justify-content: center;
  }
  .card {
    position: relative;
    width: 500px; height: 860px;
    border-radius: 22px;
    overflow: hidden;
    background: var(--card-black);
    box-shadow: 0 10px 30px rgba(0,0,0,0.18);
  }
  .card__top {
    position: absolute; left: 0; top: 0;
    width: 100%; height: 268px;
    background: var(--card-white);
    display: flex; align-items: center; justify-content: center;
  }
  .brand {
    display: flex; align-items: center; gap: 14px;
    font-family: "Cinzel", serif;
    font-weight: 700;
    font-size: 30px;
    letter-spacing: 1px;
    color: var(--ink-dark);
    text-align: center;
    line-height: 1.1;
  }
  .brand__mark {
    width: 26px; height: 26px;
    background: var(--ink-dark);
    flex: none;
  }
  .company-name {
    position: absolute;
    right: 38px; top: 300px;
    font-family: "Cinzel", serif;
    font-weight: 400;
    font-size: 33px;
    letter-spacing: 2px;
    line-height: 1.25;
    color: var(--ink-light);
    text-align: right;
  }
  .contact-frame {
    position: absolute;
    left: 26px; right: 26px; bottom: 26px;
    height: 330px;
  }
  .contact-frame svg { position: absolute; inset: 0; }
  .contact {
    position: absolute;
    font-family: "Arimo", sans-serif;
    font-size: 15px;
    color: var(--ink-light);
    white-space: nowrap;
  }
  .contact--address { left: 28px; top: 108px; }
  .contact--phone {
    left: 0; right: 0; top: 158px;
    text-align: center;
  }
  .contact--email { left: 12px; top: 198px; font-size: 14.5px; }
</style>
</head>
<body>
  <main class="canvas">
    <article class="card">
      <header class="card__top">
        <div class="brand">
          <span class="brand__mark"></span>
          <span class="brand__name">PEARLWOOD<br>FRAMING</span>
        </div>
      </header>

      <h1 class="company-name">PEARLWOOD FRAMING<br>WORKS</h1>

      <section class="contact-frame">
        <svg width="448" height="330" viewBox="0 0 448 330" aria-hidden="true">
          <rect x="1.5" y="1.5" width="445" height="327" rx="42" ry="42"
                fill="none" stroke="var(--frame-navy)" stroke-width="3"/>
          <line x1="2" y1="167" x2="158" y2="167" stroke="var(--frame-navy)" stroke-width="2.5"/>
          <line x1="290" y1="167" x2="446" y2="167" stroke="var(--frame-navy)" stroke-width="2.5"/>
        </svg>
        <p class="contact contact--address">7732 FERNGLEN PASS LN AUSTIN, TX 78734</p>
        <p class="contact contact--phone">(512)555-0193</p>
        <p class="contact contact--email">PEARLWOODFRAMINGWORKS@MAILNEST.EXAMPLE</p>
      </section>
    </article>
  </main>
</body>
</html>
```